brovlanepass.net

Develop a website for brolanepass.net will be a site to sell tickets for concerts, shows, shows, theaters and others. I need a web design easy view, very easy to use and accumulate events by date. The aim is to develop the site was connected to a complex system that is already developed. (Important this page to a robust system was connected via links the idea is to develop only the front view)
Updates

Reason: I need more designs yet we have not made the decision

Target Market(s)

millennials, adults, who want to enjoy concerts and shows

Industry/Entity Type

Event

Number of Pages Required

5+ page

Colors
1b1b1b
aaaaaa
ffffff

Requirements
Must have
• Easy Vista, accumulation of upcoming events, past events. The tabs should have are: 1 Start: In this part of upcoming events occur. You could put a banner on the top and down the events by date. 2. How to order: page with instructions on how to purchase tickets 3. About Us: The company history 4. Contact: Phones and template for contact by mail 5. Our policies: shopping 6. Notice Privacy: Privacy Notice Copoy 7. Centers Sale: physical places where they can purchase tickets Promoters 8. access: Link to a template
Nice to have
• as you can see p www.quimbarostage.net or farunda.net or farunda.org or gallowmerk.net (important this page to a robust system was connected via links the idea is to develop only the front view)
Should not have
• Many things Tangled

```html
<!DOCTYPE html>
<html lang="en">
<head>
<meta charset="utf-8">
<title>brovlanepass</title>
<link rel="stylesheet" href="https://fonts.googleapis.com/css2?family=Open+Sans:wght@300;400;600;700&family=Ubuntu:wght@400;500&display=swap">
<style>
:root{
  --page:#1b1b1b;
  --bar:#262626;
  --line:#3a3a3a;
  --panel:#ebebeb;
  --muted:#aaaaaa;
  --ink:#222222;
  --body-ink:#444444;
  --white:#ffffff;
}
*{box-sizing:border-box;margin:0;padding:0}
html,body{width:747px;height:1200px;overflow:hidden;background:var(--page);font-family:"Open Sans",sans-serif;color:var(--muted)}
.topbar{height:28px;background:var(--bar);border-bottom:1px solid #111;position:relative}
.search{position:absolute;left:82px;top:3px;width:150px;height:22px;background:#333;border:1px solid #3c3c3c;font-size:7px;color:#8a8a8a;padding:6px 9px;display:flex;justify-content:space-between;align-items:center}
.social-top{position:absolute;left:451px;top:4px;display:flex;gap:5px}
.social-top span{width:20px;height:20px;border:1px solid #555;border-radius:50%}
.account{position:absolute;left:582px;top:9px;font-size:6.5px;color:#bbb;display:flex;gap:16px}
.account span::before{content:"";display:inline-block;width:5px;height:5px;border-radius:50%;background:#bbb;margin-right:3px;vertical-align:middle}
.header{height:70px;position:relative}
.logo{position:absolute;left:82px;top:19px;font-family:"Ubuntu",sans-serif;font-size:27px;color:#e6e6e6;letter-spacing:.3px}
.nav{position:absolute;right:82px;top:30px;display:flex;gap:14px;font-size:7px;color:var(--muted)}
.nav .active{color:var(--white);text-decoration:underline}
.main{width:583px;margin-left:82px;background:var(--panel)}
.hero{height:248px;position:relative;background:radial-gradient(ellipse at 28% 18%,#c9a070 0%,#6e5538 22%,#2b2621 55%,#151719 100%)}
.hero-sub{position:absolute;left:14px;top:68px;font-weight:300;font-size:16px;color:#f2f2f2}
.hero-title{position:absolute;left:14px;top:89px;font-weight:700;font-size:18px;color:#fff;letter-spacing:.6px}
.buy{position:absolute;left:15px;top:116px;width:60px;height:22px;background:#fff;color:#222;font-size:9px;display:flex;align-items:center;justify-content:center;border-radius:2px}
.dots{position:absolute;left:266px;bottom:-5px;width:50px;height:10px;background:#444;border-radius:5px;display:flex;gap:6px;justify-content:center;align-items:center}
.dots i{width:4px;height:4px;border-radius:50%;border:1px solid #fff}
.dots i:first-child{background:#fff}
.ads{display:flex;gap:27px;padding:16px 0 0 56px;height:46px}
.ad{height:30px}
.ad-appeal{width:210px;background:linear-gradient(90deg,#b8302c 0 30%,#1d1d1d 30% 100%)}
.ad-health{width:234px;background:linear-gradient(90deg,#2a2a2a 0 14%,#2f6fb2 14% 76%,#f1f1f1 76% 100%)}
.section-head{display:flex;justify-content:space-between;align-items:center;padding:14px 7px 0 7px;height:40px}
.section-head h2{font-family:"Ubuntu",sans-serif;font-weight:400;font-size:15.5px;color:#222}
.view-all{font-size:5.5px;color:#666;border:1px solid #ccc;background:#fff;padding:4px 8px}
.grid{display:grid;grid-template-columns:repeat(4,136px);column-gap:8px;row-gap:21px;padding:8px 8px 0 8px;height:622px}
.event .thumb{height:136px}
.event .date{font-size:8.5px;color:#222;margin:9px 0 0 1px}
.event .desc{font-size:7.6px;line-height:10.5px;color:#555;margin-top:3px}
.event .loc{font-size:5.8px;color:#888;margin-top:3px;display:flex;align-items:center;gap:3px}
.footer{height:97px;position:relative}
.flinks{position:absolute;left:82px;top:19px;display:grid;grid-template-columns:68px 68px;row-gap:7px;font-size:6.3px;color:#bbb}
.flinks span::before{content:"• ";color:#888}
.newsletter{position:absolute;left:306px;top:18px}
.newsletter h3{font-weight:400;font-size:8px;color:#ddd}
.subscribe{display:flex;margin-top:8px}
.subscribe .field{width:135px;height:26px;background:#fff;font-size:6.5px;color:#999;padding:9px 11px}
.subscribe .btn{width:60px;height:26px;background:#3a3a3a;color:#eee;font-size:8px;display:flex;align-items:center;justify-content:center}
.social{position:absolute;left:617px;top:18px}
.social h3{font-weight:400;font-size:8px;color:#ddd}
.social .row{display:flex;gap:5px;margin-top:7px}
.social .row span{width:16px;height:16px;border-radius:50%}
.blue{background:#3b63a8}.sky{background:#2a9be0}.red{background:#d4392e}
.copyright{border-top:1px solid var(--line);height:35px;text-align:center;font-size:6.8px;color:#bbb;padding-top:13px}
</style>
</head>
<body>
<div class="topbar">
  <div class="search">Search event, artist, location... <svg width="8" height="8" viewBox="0 0 8 8"><circle cx="3.3" cy="3.3" r="2.4" fill="none" stroke="#888" stroke-width="1"/><line x1="5" y1="5" x2="7.5" y2="7.5" stroke="#888"/></svg></div>
  <div class="social-top"><span></span><span></span><span></span><span></span><span></span></div>
  <div class="account"><span>My Account</span><span>Help</span></div>
</div>
<header class="header">
  <div class="logo">brovlanepass</div>
  <nav class="nav"><span class="active">Home</span><span>How to Order</span><span>About us</span><span>Contact us</span><span>Policies</span><span>Privacy</span><span>Center Sale</span><span>Access</span></nav>
</header>
<main class="main">
  <section class="hero" role="img" aria-label="Concert crowd with raised hands in warm stage light">
    <div class="hero-sub">Pellentesque urna ligula</div>
    <div class="hero-title">FEUGIAT VITAE MATTIS</div>
    <div class="buy">Buy Ticket</div>
    <div class="dots"><i></i><i></i><i></i><i></i></div>
  </section>
  <div class="ads">
    <div class="ad ad-appeal" role="img" aria-label="Relief appeal advertising banner"></div>
    <div class="ad ad-health" role="img" aria-label="Family health campaign advertising banner"></div>
  </div>
  <div class="section-head"><h2>Upcoming Events</h2><span class="view-all">View All »</span></div>
  <div class="grid">
    <div class="event"><div class="thumb" role="img" aria-label="Box office storefront on a busy street" style="background:linear-gradient(160deg,#7e95b8,#b94747 55%,#8a8a8a)"></div><div class="date">20 Mar, 2017</div><div class="desc">Cras vel tortor imperdiet, pharetra erat non, efficitur tellus</div><div class="loc"><svg width="4" height="6" viewBox="0 0 4 6"><path d="M2 6 0.3 2.6A1.8 1.8 0 1 1 3.7 2.6Z" fill="#999"/></svg>Pellentesque convallis diam efficitur</div></div>
    <div class="event"><div class="thumb" role="img" aria-label="Jazz band performing with saxophone" style="background:linear-gradient(160deg,#2c3848,#4d4a44 50%,#1d2026)"></div><div class="date">20 Mar, 2017</div><div class="desc">Cras vel tortor imperdiet, pharetra erat non, efficitur tellus</div><div class="loc"><svg width="4" height="6" viewBox="0 0 4 6"><path d="M2 6 0.3 2.6A1.8 1.8 0 1 1 3.7 2.6Z" fill="#999"/></svg>Pellentesque convallis diam efficitur</div></div>
    <div class="event"><div class="thumb" role="img" aria-label="Colour powder festival crowd" style="background:linear-gradient(160deg,#5fb7d8,#c85fae 45%,#d9c84a 75%,#5c9b55)"></div><div class="date">20 Mar, 2017</div><div class="desc">Cras vel tortor imperdiet, pharetra erat non, efficitur tellus</div><div class="loc"><svg width="4" height="6" viewBox="0 0 4 6"><path d="M2 6 0.3 2.6A1.8 1.8 0 1 1 3.7 2.6Z" fill="#999"/></svg>Pellentesque convallis diam efficitur</div></div>
    <div class="event"><div class="thumb" role="img" aria-label="Rock band playing guitars on stage" style="background:radial-gradient(circle at 30% 30%,#e2b070,#7a4f30 45%,#1c1815)"></div><div class="date">20 Mar, 2017</div><div class="desc">Cras vel tortor imperdiet, pharetra erat non, efficitur tellus</div><div class="loc"><svg width="4" height="6" viewBox="0 0 4 6"><path d="M2 6 0.3 2.6A1.8 1.8 0 1 1 3.7 2.6Z" fill="#999"/></svg>Pellentesque convallis diam efficitur</div></div>
    <div class="event"><div class="thumb" role="img" aria-label="Singer with microphone under purple light" style="background:linear-gradient(150deg,#d9337f,#7d2ba8 50%,#2b1c6a)"></div><div class="date">20 Mar, 2017</div><div class="desc">Cras vel tortor imperdiet, pharetra erat non, efficitur tellus</div><div class="loc"><svg width="4" height="6" viewBox="0 0 4 6"><path d="M2 6 0.3 2.6A1.8 1.8 0 1 1 3.7 2.6Z" fill="#999"/></svg>Pellentesque convallis diam efficitur</div></div>
    <div class="event"><div class="thumb" role="img" aria-label="Empty venue with rows of white chairs" style="background:linear-gradient(180deg,#5a5752,#9d9a94 45%,#e4e4e4)"></div><div class="date">20 Mar, 2017</div><div class="desc">Cras vel tortor imperdiet, pharetra erat non, efficitur tellus</div><div class="loc"><svg width="4" height="6" viewBox="0 0 4 6"><path d="M2 6 0.3 2.6A1.8 1.8 0 1 1 3.7 2.6Z" fill="#999"/></svg>Pellentesque convallis diam efficitur</div></div>
    <div class="event"><div class="thumb" role="img" aria-label="Hands raised against bright stage lights" style="background:radial-gradient(circle at 40% 30%,#f4e2b8,#c98a3c 35%,#2c2a2e 80%)"></div><div class="date">20 Mar, 2017</div><div class="desc">Cras vel tortor imperdiet, pharetra erat non, efficitur tellus</div><div class="loc"><svg width="4" height="6" viewBox="0 0 4 6"><path d="M2 6 0.3 2.6A1.8 1.8 0 1 1 3.7 2.6Z" fill="#999"/></svg>Pellentesque convallis diam efficitur</div></div>
    <div class="event"><div class="thumb" role="img" aria-label="Popcorn bucket and 3D glasses on a red surface" style="background:linear-gradient(180deg,#1d3b5a,#2d5878 60%,#8a1f3c)"></div><div class="date">20 Mar, 2017</div><div class="desc">Cras vel tortor imperdiet, pharetra erat non, efficitur tellus</div><div class="loc"><svg width="4" height="6" viewBox="0 0 4 6"><path d="M2 6 0.3 2.6A1.8 1.8 0 1 1 3.7 2.6Z" fill="#999"/></svg>Pellentesque convallis diam efficitur</div></div>
    <div class="event"><div class="thumb" role="img" aria-label="Cinema audience in red seats" style="background:linear-gradient(180deg,#2a0f10,#a31c1e 50%,#3b1010)"></div><div class="date">20 Mar, 2017</div><div class="desc">Cras vel tortor imperdiet, pharetra erat non, efficitur tellus</div><div class="loc"><svg width="4" height="6" viewBox="0 0 4 6"><path d="M2 6 0.3 2.6A1.8 1.8 0 1 1 3.7 2.6Z" fill="#999"/></svg>Pellentesque convallis diam efficitur</div></div>
    <div class="event"><div class="thumb" role="img" aria-label="Singer performing into a microphone" style="background:linear-gradient(150deg,#3a6ec0,#8f4cb0 50%,#c98a56)"></div><div class="date">20 Mar, 2017</div><div class="desc">Cras vel tortor imperdiet, pharetra erat non, efficitur tellus</div><div class="loc"><svg width="4" height="6" viewBox="0 0 4 6"><path d="M2 6 0.3 2.6A1.8 1.8 0 1 1 3.7 2.6Z" fill="#999"/></svg>Pellentesque convallis diam efficitur</div></div>
    <div class="event"><div class="thumb" role="img" aria-label="Two girls singing karaoke" style="background:linear-gradient(150deg,#5c5a5e,#9b7d70 50%,#3a3438)"></div><div class="date">20 Mar, 2017</div><div class="desc">Cras vel tortor imperdiet, pharetra erat non, efficitur tellus</div><div class="loc"><svg width="4" height="6" viewBox="0 0 4 6"><path d="M2 6 0.3 2.6A1.8 1.8 0 1 1 3.7 2.6Z" fill="#999"/></svg>Pellentesque convallis diam efficitur</div></div>
    <div class="event"><div class="thumb" role="img" aria-label="Festival crowd cheering under colourful lights" style="background:radial-gradient(circle at 50% 30%,#e8e2a0,#6fa850 35%,#2d3a58 70%,#141414)"></div><div class="date">20 Mar, 2017</div><div class="desc">Cras vel tortor imperdiet, pharetra erat non, efficitur tellus</div><div class="loc"><svg width="4" height="6" viewBox="0 0 4 6"><path d="M2 6 0.3 2.6A1.8 1.8 0 1 1 3.7 2.6Z" fill="#999"/></svg>Pellentesque convallis diam efficitur</div></div>
  </div>
</main>
<footer>
  <div class="footer">
    <div class="flinks"><span>Home</span><span>Policies</span><span>How to Order</span><span>Privacy</span><span>About us</span><span>Center Sale</span><span>Contact us</span><span>Access</span></div>
    <div class="newsletter"><h3>Newsletter Subscribe</h3><div class="subscribe"><div class="field">Email Address</div><div class="btn">SUBSCRIBE</div></div></div>
    <div class="social"><h3>Social Media</h3><div class="row"><span class="blue"></span><span class="sky"></span></div><div class="row"><span class="red"></span><span class="red"></span></div></div>
  </div>
  <div class="copyright">Copyright © 2017 Company name. All rights reserved.</div>
</footer>
</body>
</html>
```